Impack Proof Screen Protector Packaging Design Project

I want a sleek box design for an Impact Proof Screen Protection Shield" for mobile phones and tablet screens. Want to use this design for online website sale (eCommerce). Please use the colour combination which can effect customers physiology immediately.
Product Features:
Name: vemu Tallguard
Advanced Impact Protection Shield
Easy and Fast Application
Compatible With Stylus
Guaranteed Glue Free
Perfect Crystal Clear
Anti Fingerprint
No Air Bubble
Anti Bacterial
Anti scratch

come on guys...give me some best designs please

Project Deadline Extended
Reason: Have not received the best design yet...

Project Deadline Extended
Reason: still waiting for the best design

Project Deadline Extended

Project Deadline Extended

Project Deadline Extended

Hi,

Thanks for the design. I would like to make some changes.

I want main core colour black (HTML code of Black is 111C24)
Blue colour as aditional or second colour, (HTML code of BLUE is 0088CE)

AND another colour like Orange (HTML -> FF5800)  or Purple (HTML -> 9B1889) can be use as a ACCENT colour if needed.

Pure White, Silver and Greys like -> HTML codes -> 4D4F53 , D1D4D3 , AND C4D9E4 Can be use as support colours if needed.

please work on it and get back to me .

Thanks

Project Deadline Extended
Reason: work pending

UK & Europe is priority and then Global market

Online

• All features must write with Pictures/thumbnail on back side.
Must have a hanger hook / hole.
Must have Recycling sign/logo on the edge.
Must have our website name "vemu.co" on somewhere
its a sleek box design, size - This packing will be in 2 sizes:
a). 27cm X 11cm X 2cm
b). 25cm X 20cm X 2cm
• Impact Protection is main feature in this product, so can be highlighted with some weapon like sword or something like this...
• Please try to not use a picture of any device like lumapad etc. because this packing will be use for number of different king of mobile phone/tablet devices.

```html
<!DOCTYPE html>
<html lang="en">
<head>
<meta charset="utf-8">
<title>vemu Tallguard – Box Layout</title>
<link href="https://fonts.googleapis.com/css2?family=Open+Sans:wght@400;600;700;800&display=swap" rel="stylesheet">
<style>
  :root {
    --ink: #070101;
    --night: #140303;
    --crimson: #a3190a;
    --scarlet: #c92a0c;
    --flame: #ff5800;
    --ember: #ff8a1e;
    --gold: #ffb347;
    --cream: #fff3dc;
    --shadow: rgba(40, 4, 0, 0.95);
  }
  * { box-sizing: border-box; margin: 0; padding: 0; }
  html, body { width: 1200px; height: 682px; overflow: hidden; background: #1a0402; }
  body { font-family: "Open Sans", Arial, sans-serif; }

  .box-layout {
    position: relative;
    width: 1200px;
    height: 682px;
    overflow: hidden;
    background:
      linear-gradient(172deg, transparent 54%, rgba(255, 120, 30, 0.55) 58%, rgba(255, 88, 0, 0.15) 63%, transparent 68%),
      radial-gradient(ellipse 70% 60% at 60% 20%, var(--scarlet) 0%, var(--crimson) 40%, #4a0a04 80%, var(--night) 100%);
  }

  /* ---------- Back panel ---------- */
  .back-panel {
    position: absolute;
    left: 26px; top: 26px;
    width: 498px; height: 630px;
    background:
      linear-gradient(176deg, var(--ink) 0%, var(--ink) 50%, #3a0a03 60%, #7a2206 66%, #2a0703 76%, #0c0202 100%);
    box-shadow: 0 0 14px 4px rgba(255, 100, 20, 0.75), 0 0 40px 10px rgba(255, 70, 0, 0.35);
  }
  .back-panel__foot {
    position: absolute; left: 0; right: 0; bottom: 0; height: 92px;
    background: linear-gradient(180deg, #0e0302, #1a0503);
  }
  .feature-table { position: absolute; left: 29px; top: 37px; width: 460px; }
  .feature-row { display: flex; height: 26px; align-items: flex-start; }
  .feature-row__title {
    width: 136px; font-size: 9px; font-weight: 700; color: var(--ember);
    text-shadow: 0 0 2px #000; letter-spacing: -0.1px;
  }
  .feature-row__text { width: 320px; font-size: 6.3px; line-height: 8px; color: var(--flame); }

  .back-brand { position: absolute; right: 20px; top: 326px; text-align: right; }
  .back-brand__name { font-size: 36px; font-weight: 800; color: var(--ember); line-height: 1; }
  .back-brand__tagline { margin-top: 26px; font-size: 15px; font-weight: 600; color: var(--gold); }

  .contact { position: absolute; left: 188px; top: 428px; width: 300px; color: var(--flame); font-size: 6.3px; line-height: 8px; }
  .contact__heading { font-weight: 700; text-transform: uppercase; margin-top: 6px; }
  .contact__line { display: flex; align-items: center; gap: 7px; margin-top: 9px; }
  .contact__line svg { width: 8px; height: 8px; }
  .seal-frame { position: absolute; left: 394px; top: 574px; width: 50px; height: 30px; border-right: 1px solid #6a1a08; border-bottom: 1px solid #6a1a08; }
  .seal-mark { position: absolute; left: 456px; top: 585px; width: 14px; height: 14px; border-radius: 50%; background: #8a2408; }

  /* ---------- Spines ---------- */
  .spine {
    position: absolute; top: 0; height: 682px; background: var(--ink);
    display: flex; justify-content: center;
  }
  .spine--left { left: 557px; width: 44px; }
  .spine--right { left: 1154px; width: 46px; }
  .spine__name {
    writing-mode: vertical-rl; margin-top: 168px;
    font-size: 28px; font-weight: 800; color: var(--ember); letter-spacing: 1px;
  }

  /* ---------- Front panel ---------- */
  .front-panel { position: absolute; left: 601px; top: 0; width: 553px; height: 682px; }
  .badge-new { position: absolute; left: 448px; top: 28px; width: 76px; height: 76px; }
  .streak-art {
    position: absolute; left: 440px; top: 128px; width: 68px; height: 166px;
    background: radial-gradient(ellipse 50% 50% at 50% 50%, rgba(255, 170, 80, 0.45) 0%, rgba(255, 88, 0, 0.18) 55%, transparent 100%);
  }
  .feature-list { position: absolute; left: 23px; top: 172px; list-style: none; }
  .feature-list li {
    height: 25px; font-size: 16px; font-weight: 600; color: var(--cream);
    text-shadow: 1px 1px 0 var(--shadow), -1px 0 1px var(--shadow), 0 0 3px var(--shadow);
  }
  .front-brand__tagline {
    position: absolute; right: 10px; top: 522px;
    font-size: 15px; font-weight: 600; color: var(--cream);
    text-shadow: 1px 1px 0 var(--shadow);
  }
  .front-brand__name {
    position: absolute; left: 15px; top: 548px;
    font-size: 40px; font-weight: 800; color: var(--cream); line-height: 1;
  }
  .glue-free {
    position: absolute; left: 352px; top: 601px;
    font-size: 15px; font-weight: 700; color: var(--cream);
    text-shadow: 1px 1px 0 var(--shadow), -1px 0 1px var(--shadow), 0 0 3px var(--shadow);
  }
</style>
</head>
<body>
<main class="box-layout">

  <section class="back-panel">
    <div class="back-panel__foot"></div>

    <div class="feature-table">
      <div class="feature-row"><span class="feature-row__title">Easy and Fast Application</span><span class="feature-row__text">Smooth it on in seconds with no tools needed. Line up the edge, press down gently and the shield settles flat.</span></div>
      <div class="feature-row"><span class="feature-row__title">Compatible With Stylus</span><span class="feature-row__text">Works with every stylus and finger touch without any loss in feel.</span></div>
      <div class="feature-row"><span class="feature-row__title">Perfect Crystal Clear</span><span class="feature-row__text">Optical grade film keeps the screen bright and sharp. Colours stay true under any light.</span></div>
      <div class="feature-row"><span class="feature-row__title">Anti Fingerprint</span><span class="feature-row__text">Oil resistant coating keeps prints off the surface.</span></div>
      <div class="feature-row"><span class="feature-row__title">No Air Bubble</span><span class="feature-row__text">Self adhesive layer pushes air out as it lays down, leaving a clean finish edge to edge.</span></div>
      <div class="feature-row"><span class="feature-row__title">Anti Bacterial</span><span class="feature-row__text">Treated surface limits germ growth on the screen. Safe for daily handling by the whole family.</span></div>
      <div class="feature-row"><span class="feature-row__title">Anti Scratch</span><span class="feature-row__text">Hard coat layer resists keys, coins and daily wear.</span></div>
    </div>

    <div class="back-brand">
      <div class="back-brand__name">vemu Tallguard</div>
      <div class="back-brand__tagline">Advanced Impact Protection Shield</div>
    </div>

    <div class="contact">
      <p class="contact__heading">Product info</p>
      <p>Impact shields built for daily use on phones and tablets of every size. Fits most screens.</p>
      <p class="contact__heading">Contact</p>
      <p>Write to our team for help with fitting or returns. We reply within one working day.</p>
      <p class="contact__line">
        <svg viewBox="0 0 8 8" aria-hidden="true"><rect x="0.5" y="1.5" width="7" height="5" fill="none" stroke="#ff5800" stroke-width="1"/><path d="M0.5 1.5 L4 4.5 L7.5 1.5" fill="none" stroke="#ff5800" stroke-width="0.8"/></svg>
        <span>+44 1632 960 418</span>
      </p>
      <p class="contact__line">
        <svg viewBox="0 0 8 8" aria-hidden="true"><path d="M1.5 0.8 L3 0.8 L3.6 2.6 L2.6 3.3 Q3.4 4.9 4.8 5.5 L5.5 4.5 L7.2 5.1 L7.2 6.6 Q3.5 7.2 1 2.4 Z" fill="#ff5800"/></svg>
        <span>hello@vemu.co</span>
      </p>
    </div>

    <div class="seal-frame"></div>
    <div class="seal-mark"></div>
  </section>

  <aside class="spine spine--left">
    <span class="spine__name">vemu Tallguard</span>
  </aside>

  <section class="front-panel">
    <svg class="badge-new" viewBox="0 0 58 58" aria-label="New badge">
      <polygon fill="#ff8a1e" stroke="#fff3dc" stroke-width="2"
        points="29,2 34,12 45,7 44,19 56,21 47,30 56,38 44,40 45,51 34,46 29,56 24,46 13,51 14,40 2,38 11,30 2,21 14,19 13,7 24,12"/>
      <text x="29" y="34" text-anchor="middle" font-family="Open Sans, Arial, sans-serif" font-size="13" font-weight="800" fill="#fff3dc" stroke="#7a1a04" stroke-width="0.6">NEW</text>
    </svg>

    <div class="streak-art" role="img" aria-label="Illustration area: glowing comet striking the screen to suggest impact"></div>

    <ul class="feature-list">
      <li>Easy and Fast Application</li>
      <li>Compatible With Stylus</li>
      <li>Perfect Crystal Clear</li>
      <li>Anti Fingerprint</li>
      <li>No Air Bubble</li>
      <li>Anti Bacterial</li>
      <li>Anti scratch</li>
    </ul>

    <div class="front-brand__tagline">Advanced Impact Protection Shield</div>
    <div class="front-brand__name">vemu Tallguard</div>
    <div class="glue-free">Guaranteed Glue Free</div>
  </section>

  <aside class="spine spine--right">
    <span class="spine__name">vemu Tallguard</span>
  </aside>

</main>
</body>
</html>
```